New letter head for Air Conditioning business

We need a new professional letter head design to suit our new re-branded air conditioning business. Our new logo is attached

```html
<!DOCTYPE html>
<html lang="en">
<head>
<meta charset="utf-8">
<title>Norvale Letterhead</title>
<link rel="stylesheet" href="https://fonts.googleapis.com/css2?family=Lato:wght@400;700&family=Open+Sans:wght@400;600&display=swap">
<style>
  :root {
    --paper: #ffffff;
    --ink: #4a4a4a;
    --ink-dark: #222222;
    --brand-green: #3fb36b;
    --brand-coral: #ee6a5a;
    --brand-grey: #3a3a3c;
    --pattern-grey: #d6d6d6;
    --pattern-green: #dff2e5;
    --pattern-coral: #fbe1dd;
  }
  * { margin: 0; padding: 0; box-sizing: border-box; }
  html, body { width: 1040px; height: 1200px; overflow: hidden; background: var(--paper); }
  .letterhead {
    position: relative;
    width: 1040px;
    height: 1200px;
    background: var(--paper);
    font-family: "Open Sans", Arial, sans-serif;
    color: var(--ink);
  }
  .brand {
    position: absolute;
    left: 94px;
    top: 46px;
    display: flex;
    align-items: center;
    gap: 16px;
  }
  .brand-dot {
    width: 54px; height: 54px;
    border-radius: 50%;
    background: var(--brand-green);
  }
  .brand-name {
    font-family: "Lato", Arial, sans-serif;
    font-weight: 700;
    font-size: 46px;
    letter-spacing: 4px;
    color: var(--brand-grey);
  }
  .contact {
    position: absolute;
    right: 100px;
    top: 52px;
    text-align: right;
    font-family: "Lato", Arial, sans-serif;
    font-style: normal;
    font-size: 19px;
    line-height: 23px;
    color: var(--ink-dark);
  }
  .contact .label { color: var(--brand-green); }
  .header-rule {
    position: absolute;
    left: 104px; top: 128px;
    width: 836px; height: 3px;
    background: var(--brand-green);
  }
  .letter-body {
    position: absolute;
    left: 99px;
    width: 841px;
    font-size: 15px;
  }
  .issue-date { top: 218px; }
  .recipient { top: 254px; line-height: 18px; }
  .salutation { top: 358px; }
  .content { top: 410px; font-size: 16.5px; }
  .content p {
    text-align: justify;
    line-height: 27px;
    margin-bottom: 27px;
  }
  .closing { top: 815px; }
  .signature-mark {
    display: block;
    width: 230px; height: 30px;
    margin: 12px 0 10px;
    background: linear-gradient(90deg, #eeeeee, #f6f6f6);
  }
  .signer-name { font-size: 19px; font-weight: 600; color: var(--ink-dark); }
  .signer-role { margin-top: 6px; }
  .address {
    position: absolute;
    left: 97px; top: 1130px;
    font-family: "Lato", Arial, sans-serif;
    font-size: 18px;
    line-height: 22px;
    color: var(--ink-dark);
  }
  .footer-bar {
    position: absolute;
    left: 96px; bottom: 0;
    width: 195px; height: 12px;
    background: var(--brand-coral);
  }
  .footer-pattern {
    position: absolute;
    right: 0; bottom: 0;
    width: 345px; height: 218px;
    background: linear-gradient(135deg, transparent 18%, var(--pattern-green) 45%, var(--pattern-grey) 70%, var(--pattern-coral) 100%);
    opacity: 0.7;
    clip-path: polygon(100% 0, 100% 100%, 0 100%);
  }
</style>
</head>
<body>
  <main class="letterhead">
    <header>
      <div class="brand">
        <span class="brand-dot"></span>
        <span class="brand-name">NORVALE</span>
      </div>
      <address class="contact">
        <div><span class="label">Phone:</span> 044-987 210 354</div>
        <div><span class="label">Email:</span> hello@norvalecool.com</div>
        <div><span class="label">Web:</span> www.norvalecool.com</div>
      </address>
      <div class="header-rule"></div>
    </header>

    <div class="letter-body issue-date">Issuing Date: May 5, 2018</div>
    <div class="letter-body recipient">
      Name Of Employee Mr. XYZABC<br>
      Address of Employee<br>
      Address Line 2 etc..
    </div>
    <div class="letter-body salutation">Dear Mr.XYZABC</div>

    <section class="letter-body content">
      <p>Lorem Ipsum has been the industry's standard dummy text ever since the 1500s, when an unknown printer took a galley of type and scrambled it to make a type specimen book. It has survived not only five centuries, but also the leap into electronic typesetting, remaining essentially unchanged. It was popularised in the 1960s with the release of Typeline sheets containing Lorem Ipsum passages, and more recently with desktop publishing software like Corvan PageSetter including versions of Lorem Ipsum.</p>
      <p>Lorem Ipsum is simply dummy text of the printing and typesetting industry. Lorem Ipsum has been the industry's standard dummy text ever since the 1500s, when an unknown printer took a galley of type and scrambled it to make a type specimen book.</p>
      <p>It has survived not only five centuries, but also the leap into electronic typesetting, remaining essentially unchanged. It was popularised in the 1960s with the release of Typeline sheets containing Lorem IpsumIpsum passages.</p>
    </section>

    <section class="letter-body closing">
      <div>Yours Sincerely</div>
      <span class="signature-mark" role="img" aria-label="Handwritten signature of the managing director"></span>
      <div class="signer-name">Marcus Ellery</div>
      <div class="signer-role">Managing Director</div>
    </section>

    <footer>
      <div class="address">421, Address line here<br>Country Name, 45452</div>
      <div class="footer-bar"></div>
      <div class="footer-pattern" role="img" aria-label="Faint repeating brand pattern in grey, green and coral"></div>
    </footer>
  </main>
</body>
</html>
```